Business card design needed

I am a local business in the Blue Mountains area of Sydney. I am a sole trader and the business has been operating 7 months. To date the business has been built on referrals only and all my clinets for both home & commercial services are themselves business owners. I specialise in Home and Office cleaning and small business cleaning for example cafes, restuarants, health clinics.
I would like a clean looking design( maybe a white background). If its possible(not madatory) to incorporate a duster, or mop & bucket into the design or roof tops to communicate business premises that would be great. I would like my clients to know what the business is from the card. My uniform is navy with red/pink logo on .Attatched is the unifrom logo but it is not critical to match the font for the business card.
please put my name on contact details; Marla Quenby, Business owner.
Updates
Thank you very much to all the designers and their work efforts to submit a design for Tidal Fern Domestic Services. I have made a decision to accept the deign that Kobel Design of the United States submitted. Again Many thanks. Marla
Target Market(s)
business owners, generally women between 35-55
Industry/Entity Type
Small Business
Contact Information for Business Card
Tidal Fern Domestic Services,
specialist in Home & Small business cleaning
Wrenvale East
tel: 0412559074 0412fernly
Logo Text
Tidal Fern Domestic Servies
Logo styles of interest
Emblem Logo
Abstract Logo
Wordmark Logo
Look and feel
Each slider illustrates characteristics of the customer's brand and the style your logo design should communicate.

```html
<!DOCTYPE html>
<html lang="en">
<head>
<meta charset="utf-8">
<title>Tidal Fern Domestic Services – Business Card</title>
<link rel="stylesheet" href="https://fonts.googleapis.com/css2?family=Open+Sans:wght@400;600;700&display=swap">
<style>
  :root {
    --navy: #15116a;
    --paper: #f1f2f2;
    --white: #ffffff;
    --grid-tone: #e6e9ef;
    --bubble-pink: #f2a6e6;
    --bubble-blue: #b9d3f3;
    --bubble-lime: #e4f2a2;
  }
  html, body {
    margin: 0;
    padding: 0;
    width: 1200px;
    height: 693px;
    overflow: hidden;
    background: var(--white);
  }
  .card {
    display: block;
    width: 1200px;
    height: 693px;
    font-family: "Open Sans", Arial, sans-serif;
  }
  .card__paper { fill: var(--paper); }
  .card__strip { fill: var(--white); }
  .card__header { fill: var(--navy); }
  .logo-panel { fill: var(--grid-tone); }
  .logo-text { fill: var(--navy); font-weight: 600; }
  .header__title { fill: var(--white); font-weight: 600; font-size: 50px; }
  .header__tagline { fill: var(--white); font-weight: 400; font-size: 30px; }
  .holder__name { fill: var(--navy); font-weight: 700; font-size: 77px; }
  .holder__role { fill: var(--navy); font-weight: 400; font-size: 38px; }
  .contact { fill: var(--navy); font-weight: 400; font-size: 35px; }
  .contact--tel { font-size: 33px; }
</style>
</head>
<body>
<svg class="card" viewBox="0 0 1200 693" xmlns="http://www.w3.org/2000/svg">
  <defs>
    <radialGradient id="bubbleGlow" cx="0.45" cy="0.5" r="0.55">
      <stop offset="0" stop-color="var(--bubble-blue)" stop-opacity="0.75"/>
      <stop offset="0.45" stop-color="var(--bubble-pink)" stop-opacity="0.4"/>
      <stop offset="0.75" stop-color="var(--bubble-lime)" stop-opacity="0.25"/>
      <stop offset="1" stop-color="var(--paper)" stop-opacity="0"/>
    </radialGradient>
    <radialGradient id="cornerGlow" cx="1" cy="0" r="1">
      <stop offset="0" stop-color="#9b7fd8" stop-opacity="0.8"/>
      <stop offset="1" stop-color="var(--navy)" stop-opacity="0"/>
    </radialGradient>
  </defs>

  <rect class="card__paper" x="0" y="0" width="1200" height="693"/>
  <rect class="card__strip" x="0" y="0" width="226" height="693"/>

  <rect class="card__header" x="226" y="0" width="974" height="169"/>
  <rect x="1110" y="0" width="90" height="169" fill="url(#cornerGlow)" role="img" aria-label="Scattered soft bubble decoration"/>
  <text class="header__title" x="297" y="102">Tidal Fern Domestic Services</text>
  <text class="header__tagline" x="297" y="145">specialist in Home &amp; Small business cleaning Wrenvale East</text>

  <rect class="logo-panel" x="28" y="40" width="194" height="609" role="img" aria-label="Graph paper texture behind the wordmark"/>
  <g class="logo" transform="translate(125 345) rotate(-90)">
    <text class="logo-text" x="0" y="-10" text-anchor="middle" font-size="58">Tidal Fern</text>
    <text class="logo-text" x="0" y="52" text-anchor="middle" font-size="42">Domestic Services</text>
  </g>

  <rect x="226" y="169" width="290" height="490" fill="url(#bubbleGlow)" role="img" aria-label="Scattered pastel soap bubbles"/>

  <text class="holder__name" x="718" y="348" text-anchor="middle">Marla Quenby</text>
  <text class="holder__role" x="718" y="401" text-anchor="middle">Business owner</text>

  <text class="contact" x="260" y="581">E: tidalfern@netmailbox.com</text>
  <text class="contact" x="300" y="624">www.tidalfernclean.com.au</text>
  <text class="contact contact--tel" x="858" y="627">Tel: 0412559074</text>
</svg>
</body>
</html>
```